LEARN Business Skills so you can Earn a good living

size of the poster is 8”x 10.75" plus 0.25" bleed.
Please leave 1 inch on the bottoum for footer
I want a design a poster that will attract people's attention.
I appreciate a creative ad however the ad should not take away from being able to clearly read the text.
-I also appreciate a simple creative ad that is not too busy.
-you can use graphics, vectors, or pictures of real people.
-however, if you use real people it should be a white male that is wearing a white shirt and look like a professional person.

Target Market(s)

Potential young business people

Industry/Entity Type

education

Requirements
Must have
• easy to read the text
Nice to have
• I would like a "creative" simple ad that is easy to be read
Should not have
• pictures of women

```html
<!DOCTYPE html>
<html lang="en">
<head>
<meta charset="utf-8">
<title>Learn to Earn – Business Enrichment Course</title>
<link rel="stylesheet" href="https://fonts.googleapis.com/css2?family=Bebas+Neue&family=Montserrat:wght@500;600;700;800&display=swap">
<style>
  :root {
    --stage: #d9dadc;
    --blue: #2f5da4;
    --blue-deep: #24498a;
    --blue-light: #4a7dc6;
    --rim: #1e3f93;
    --orange: #ef5a2a;
    --yellow: #f4e61c;
    --white: #ffffff;
    --list: #3560a8;
    --footer-text: #8c8f96;
  }
  * { margin: 0; padding: 0; box-sizing: border-box; }
  html, body { width: 1200px; height: 2824px; overflow: hidden; }
  body { background: var(--stage); font-family: "Montserrat", sans-serif; position: relative; }

  .poster {
    position: absolute; left: 60px; top: 684px;
    width: 1080px; height: 1457px;
    background: linear-gradient(160deg, var(--blue-deep) 0%, var(--blue) 45%, var(--blue-light) 62%, var(--blue) 80%);
    overflow: hidden;
    box-shadow: 0 8px 30px rgba(0,0,0,.25);
  }
  .poster-frame {
    position: absolute; left: 26px; top: 26px; right: 26px; bottom: 26px;
    border: 2px solid rgba(255,255,255,.25); border-radius: 36px; pointer-events: none; z-index: 5;
  }
  .hero-photo { position: absolute; left: 0; top: 0; width: 1080px; height: 560px; }

  .ribbon { position: absolute; left: 72px; top: 0; width: 318px; height: 396px; }
  .ribbon-title {
    position: absolute; left: 72px; top: 34px; width: 318px;
    text-align: center; font-family: "Bebas Neue", sans-serif; color: var(--white); line-height: 1;
  }
  .ribbon-title .big { display: block; font-size: 140px; letter-spacing: 1px; }
  .ribbon-title .small { display: block; font-size: 48px; letter-spacing: 4px; margin: 2px 0 4px; }

  .course-title {
    position: absolute; left: 0; top: 516px; width: 1080px;
    font-weight: 800; color: var(--white); text-transform: uppercase; line-height: 0.95;
  }
  .course-title .line1 { display: block; font-size: 82px; padding-left: 128px; }
  .course-title .line2 { display: block; font-size: 82px; text-align: center; margin-top: 6px; letter-spacing: 1px; }
  .tagline {
    position: absolute; left: 0; top: 702px; width: 1080px; text-align: center;
    color: var(--white); font-weight: 500; font-size: 24px; text-transform: uppercase;
  }

  .skills-box {
    position: absolute; left: 168px; top: 782px; width: 744px; height: 168px;
    border: 2px dashed rgba(255,255,255,.55);
    background: linear-gradient(180deg, #4b82c9 0%, #3b6cb6 100%);
    box-shadow: 0 10px 16px rgba(0,0,0,.3);
    text-align: center; color: var(--white); font-weight: 700; text-transform: uppercase;
  }
  .skills-box .lead { font-size: 25px; margin-top: 18px; color: #e3e9f4; }
  .skills-box .benefits { font-size: 29px; line-height: 44px; margin-top: 10px; }
  .hl { color: var(--yellow); }

  .course-area {
    position: absolute; left: 0; top: 1012px; width: 1080px; height: 445px;
    background: linear-gradient(135deg, #eef0f3 0%, #ffffff 45%, #e9ebef 100%);
  }
  .course-list { position: absolute; top: 40px; list-style: none; color: var(--list); font-weight: 500; font-size: 20px; }
  .course-list li { line-height: 30px; white-space: nowrap; }
  .course-list li::before { content: "• "; }
  .course-list.col1 { left: 50px; }
  .course-list.col1 li { line-height: 34px; }
  .course-list.col2 { left: 343px; }
  .course-list.col3 { left: 796px; }
  .col-divider { position: absolute; top: 30px; width: 2px; height: 240px; background: linear-gradient(#fff, #dfe2e7, #fff); }

  .footer-band {
    position: absolute; left: 0; top: 1307px; width: 1080px; height: 150px;
    background: linear-gradient(180deg, #e3e5e9 0%, #f4f5f7 100%);
  }
  .footer-note {
    position: absolute; left: 0; top: 56px; width: 100%; text-align: center;
    color: var(--footer-text); font-weight: 700; font-size: 28px; text-transform: uppercase;
  }
</style>
</head>
<body>
  <main class="poster">
    <svg class="hero-photo" viewBox="0 0 1080 560">
      <defs>
        <radialGradient id="photoTone" cx="0.55" cy="0.5" r="0.6">
          <stop offset="0" stop-color="#fbfbfb"/>
          <stop offset="0.7" stop-color="#e8e8ea"/>
          <stop offset="1" stop-color="#cfd1d5"/>
        </radialGradient>
      </defs>
      <circle cx="880" cy="70" r="478" fill="var(--rim)"/>
      <circle cx="880" cy="62" r="466" fill="url(#photoTone)" role="img" aria-label="Photo of a smiling professional man in a white shirt holding a laptop and a fan of banknotes"/>
    </svg>

    <svg class="ribbon" viewBox="0 0 318 396" aria-hidden="true">
      <polygon points="0,0 318,0 318,396 159,320 0,396" fill="var(--orange)"/>
    </svg>
    <h2 class="ribbon-title"><span class="big">Learn</span><span class="small">to</span><span class="big">Earn</span></h2>

    <h1 class="course-title"><span class="line1">Business</span><span class="line2">Enrichment Course</span></h1>
    <p class="tagline">A proven success of helping people in their livelihoods</p>

    <section class="skills-box">
      <p class="lead">Business skills that will help you:</p>
      <p class="benefits">Get a <span class="hl">quality job</span> &nbsp;|&nbsp; Start/Grow<br>your <span class="hl">business</span> &nbsp;|&nbsp; <span class="hl">Increase</span> your <span class="hl">salary</span></p>
    </section>

    <section class="course-area">
      <ul class="course-list col1">
        <li>Business Admiistration</li>
        <li>Investments</li>
        <li>Sales&nbsp; Marketing</li>
        <li>Public Speaking</li>
        <li>Distribution</li>
        <li>Real Estate</li>
        <li>Shopvale Selling</li>
      </ul>
      <div class="col-divider" style="left:318px"></div>
      <ul class="course-list col2">
        <li>Small Business Management</li>
        <li>Computers</li>
        <li>Business Law</li>
        <li>Import/export</li>
        <li>Marketing</li>
        <li>Health Care</li>
        <li>Project Management Interviewing Skills</li>
      </ul>
      <div class="col-divider" style="left:772px"></div>
      <ul class="course-list col3">
        <li>Finance</li>
        <li>Accounting</li>
        <li>Negotiation</li>
        <li>Information Technoloy</li>
        <li>LedgerLeaf</li>
        <li>Management</li>
      </ul>
    </section>

    <footer class="footer-band">
      <p class="footer-note">Bottoum for footer</p>
    </footer>

    <div class="poster-frame"></div>
  </main>
</body>
</html>
```